Social responsible Renewable Energy company

We at brivoX are an independent power producer company founded in 2021 that handles large scale deployment of Renewable Energy and carbon neutral Energy as a service model. We offer turnkey solutions using solar panel systems and this could be incorporated in our business cards. You can also find our logo in the documents provided. Another key issue is that the business cards will be printed on recicled paper, not sure if this is a limitation in deciding the design. The recycled sign should also be added on the business card and stating that the paper used was recycled. Our website is www.mybrivox-example.com. It should also be very professional, not too dreamy but still needs to capture your imagination. We are really excited to get your ideas !

Target Market(s)

Renewable Energy market

Contact Information for Business Card

The business card will be printed on recycled paper. Name of the company is brivoX. Website is www.mybrivox-example.com

Requirements
Nice to have
• Our motto: Powered by renewable, driven by people.

```html
<!DOCTYPE html>
<html lang="en">
<head>
<meta charset="utf-8">
<title>brivoX business card</title>
<link href="https://fonts.googleapis.com/css2?family=Open+Sans:wght@400;600;700&display=swap" rel="stylesheet">
<style>
  :root {
    --scene-bg: #3b3b3b;
    --card-bg: #151515;
    --card-edge: #2f86d6;
    --brand-blue: #2f78c6;
    --text-light: #e9e9e9;
    --pattern-dark: #101010;
    --pattern-mid: #232323;
  }
  * { box-sizing: border-box; margin: 0; padding: 0; }
  html, body {
    width: 1200px; height: 801px; overflow: hidden;
    background: var(--scene-bg);
    font-family: "Open Sans", Arial, sans-serif;
  }
  .stage {
    position: relative; width: 1200px; height: 801px;
    display: flex; align-items: center; justify-content: center; gap: 50px;
  }
  .card {
    position: relative; width: 525px; height: 300px;
    background: var(--card-bg);
    border-bottom: 3px solid var(--card-edge);
    border-left: 3px solid var(--card-edge);
    box-shadow: 0 10px 24px rgba(0,0,0,.45);
    overflow: hidden;
  }
  .wordmark {
    color: var(--brand-blue);
    font-weight: 700;
    letter-spacing: 1px;
    line-height: 1;
  }
  .card-front .wordmark {
    position: absolute; left: 52px; top: 108px; font-size: 62px;
  }
  .divider {
    position: absolute; left: 285px; top: 46px; width: 1px; height: 162px;
    background: var(--brand-blue);
  }
  .divider-cap {
    position: absolute; left: 285px; top: 46px; width: 22px; height: 1px;
    background: var(--brand-blue);
  }
  .contact {
    position: absolute; left: 305px; top: 30px; color: var(--text-light);
    font-size: 13.5px; line-height: 1.4;
  }
  .contact .person-name {
    color: var(--brand-blue); font-weight: 700; font-size: 17px;
    text-transform: uppercase; letter-spacing: .3px;
  }
  .contact .person-title { margin-bottom: 10px; }
  .contact .address { margin-bottom: 10px; }
  .contact-line { display: flex; align-items: center; gap: 7px; }
  .contact-line svg { width: 11px; height: 11px; fill: var(--text-light); flex: none; }
  .tagline {
    position: absolute; left: 0; right: 0; bottom: 26px; text-align: center;
    color: var(--text-light); font-size: 15px;
  }
  .pattern-field {
    position: absolute; inset: 0;
    background: radial-gradient(ellipse at 70% 40%, var(--pattern-mid), var(--pattern-dark) 75%);
  }
  .card-back .wordmark {
    position: absolute; right: 40px; bottom: 66px; font-size: 58px;
  }
</style>
</head>
<body>
<main class="stage">
  <section class="card card-front" aria-label="Business card front">
    <div class="wordmark">brivoX</div>
    <div class="divider"></div>
    <div class="divider-cap"></div>
    <div class="contact">
      <div class="person-name">Dan Corwell</div>
      <div class="person-title">President</div>
      <div class="address">1820 Harbor View Lane<br>Bayside CA 90000</div>
      <div class="contact-line">
        <svg viewBox="0 0 24 24" aria-hidden="true"><path d="M6.6 10.8a15.1 15.1 0 0 0 6.6 6.6l2.2-2.2a1 1 0 0 1 1-.25 11.4 11.4 0 0 0 3.6.57 1 1 0 0 1 1 1V20a1 1 0 0 1-1 1A17 17 0 0 1 3 4a1 1 0 0 1 1-1h3.5a1 1 0 0 1 1 1c0 1.25.2 2.45.57 3.6a1 1 0 0 1-.25 1z"/></svg>
        <span>555-014-2287</span>
      </div>
      <div class="contact-line">
        <svg viewBox="0 0 24 24" aria-hidden="true"><path d="M2 5h20v14H2z M2 5l10 8 10-8" fill="none" stroke="#e9e9e9" stroke-width="2"/></svg>
        <span>dcorwell@mybrivox-example.com</span>
      </div>
      <div class="contact-line">
        <svg viewBox="0 0 24 24" aria-hidden="true"><circle cx="12" cy="12" r="9" fill="none" stroke="#e9e9e9" stroke-width="2"/><path d="M3 12h18M12 3c3 3 3 15 0 18M12 3c-3 3-3 15 0 18" fill="none" stroke="#e9e9e9" stroke-width="1.6"/></svg>
        <span>www.mybrivox-example.com</span>
      </div>
    </div>
    <p class="tagline">We offer turnkey solutions using solar panel systems</p>
  </section>

  <section class="card card-back" aria-label="Business card back">
    <div class="pattern-field" role="img" aria-label="Faint embossed repeating brand pattern across the card"></div>
    <div class="wordmark">brivoX</div>
  </section>
</main>
</body>
</html>
```